Whitcombe Business Card Design

The name of the business is Dario Whitcombe, CPA LLC
The service that we offer is Accounting, Tax & Consulting Services. I need it to have the following items:
Dario Whitcombe, Principal
Phone Number
Email Address
Physical Address

I have attached the company logo, one in black and one in white. Please provide a design in black background and the other in white background. Please include "Accounting, Tax & Consulting Services". I want the business card to be clean and very professional.

```html
<!DOCTYPE html>
<html lang="en">
<head>
<meta charset="utf-8">
<title>Dario Whitcombe, CPA LLC – Business Cards</title>
<link rel="stylesheet" href="https://fonts.googleapis.com/css2?family=Montserrat:wght@500;600&family=Roboto:wght@300;400&display=swap">
<style>
  :root {
    --backdrop: #2b2b2c;
    --card-dark: #1f1f21;
    --card-dark-edge: #2c2c2e;
    --card-light: #efefef;
    --ink-dark: #3a3a3d;
    --ink-light: #f2f2f2;
    --tagline: #8e8e90;
    --band-grey: #86878a;
    --brand-red: #7e1418;
  }
  * { margin: 0; padding: 0; box-sizing: border-box; }
  html, body { width: 1200px; height: 1138px; overflow: hidden; }
  body { background: var(--backdrop); position: relative; font-family: "Montserrat", sans-serif; }

  .card {
    position: absolute;
    left: 273px;
    width: 620px;
    height: 375px;
    border-radius: 16px;
    overflow: hidden;
  }
  .card--front { top: 184px; background: linear-gradient(135deg, var(--card-dark) 0%, var(--card-dark-edge) 100%); }
  .card--back { top: 606px; background: var(--card-light); }

  .brand {
    position: absolute;
    left: 0; right: 0;
    text-align: center;
  }
  .brand__square {
    display: block;
    margin: 0 auto;
    width: 56px; height: 56px;
    background: var(--brand-red);
  }
  .brand__name {
    display: block;
    font-weight: 600;
    font-size: 25px;
    letter-spacing: 0.5px;
    line-height: 1;
    white-space: nowrap;
  }
  .brand__tagline {
    display: block;
    font-weight: 500;
    font-size: 14.5px;
    letter-spacing: 1.2px;
    color: var(--tagline);
    line-height: 1;
    white-space: nowrap;
  }

  .card--front .brand { top: 126px; }
  .card--front .brand__name { color: var(--ink-light); margin-top: 36px; }
  .card--front .brand__tagline { margin-top: 13px; }

  .card--back .brand { top: 38px; }
  .card--back .brand__name { color: var(--ink-dark); margin-top: 36px; }
  .card--back .brand__tagline { margin-top: 12px; }

  .person-band {
    position: absolute;
    left: 0; right: 0;
    top: 205px; height: 73px;
    background: var(--band-grey);
    display: flex; align-items: center; justify-content: center;
    color: var(--ink-light);
  }
  .person-band__name { font-weight: 600; font-size: 20px; letter-spacing: 0.6px; }
  .person-band__role { font-family: "Roboto", sans-serif; font-weight: 300; font-size: 16px; margin-left: 16px; }

  .contact-band {
    position: absolute;
    left: 0; right: 0;
    top: 278px; bottom: 0;
    background: var(--brand-red);
    color: var(--ink-light);
    font-family: "Roboto", sans-serif;
    font-weight: 300;
    font-size: 16px;
    text-align: center;
    padding-top: 19px;
    line-height: 24px;
  }
</style>
</head>
<body>
  <section class="card card--front" aria-label="Card front">
    <div class="brand">
      <span class="brand__square" aria-hidden="true"></span>
      <span class="brand__name">DARIO WHITCOMBE, CPA, LLC</span>
      <span class="brand__tagline">ACCOUNTING, TAX &amp; CONSULTING SERVICES</span>
    </div>
  </section>

  <section class="card card--back" aria-label="Card back">
    <div class="brand">
      <span class="brand__square" aria-hidden="true"></span>
      <span class="brand__name">DARIO WHITCOMBE, CPA, LLC</span>
      <span class="brand__tagline">ACCOUNTING, TAX &amp; CONSULTING SERVICES</span>
    </div>
    <div class="person-band">
      <span class="person-band__name">DARIO WHITCOMBE</span>
      <span class="person-band__role">|&nbsp; Principal</span>
    </div>
    <div class="contact-band">
      <p>P. 828-555-0142 &nbsp;|&nbsp; E: dw@dariowhitcombellc.com &nbsp;|&nbsp; W: dariowhitcombellc.com</p>
      <p>A: 5678, Maple Avenue, Sample City, US 654321</p>
    </div>
  </section>
</body>
</html>
```